Luxury Business Card Design for High-End Window Treatments

Gilded Slatworks
Custom Plantation Shutters & Architectural Shading Systems

⸻

BACK

Daniel Trevick
Owner

Custom Interior & Exterior Window Treatments

919-555-0148
gildedslatworks.com

I have included a picture that I’m hoping we can use on the back, but I’m also wondering if you can get rid of the ladder? Should we get rid of shutters , shades and blinds underneath Gilded Slatworks?

Target Market(s)

High-end residential homeowners, custom home builders, architects, interior designers, and luxury renovation clients seeking premium plantation shutters and motorized architectural shading systems.

Industry/Entity Type

Custom Window treatments

Contact Information for Business Card

Front Gilded Slatworks Custom Plantation Shutters Motorized Architectural Shading Systems BACK Daniel Trevick Owner 919-555-0148 GildedSlatworks.com Custom Interior & Exterior Window Treatments By Appointment

Requirements
Nice to have
• Not 100% sure on nice to halves or the color but you can definitely check out my website to get a better understanding of what I’m trying to do

```html
<!DOCTYPE html>
<html lang="en">
<head>
<meta charset="utf-8">
<title>Gilded Slatworks – Business Card</title>
<link rel="stylesheet" href="https://fonts.googleapis.com/css2?family=Playfair+Display:wght@500&family=Raleway:wght@300;400&family=Kreon:wght@400&display=swap">
<style>
  :root {
    --page: #e6e4e3;
    --ink: #141414;
    --photo-dark: #101010;
    --photo-mid: #2a2724;
    --gold: #b9a862;
    --gold-back: #a68f5f;
    --gold-text: #c9b25f;
    --tag-yellow: #f2cf55;
    --cream: #eee7d8;
    --white: #f4f4f4;
  }
  * { box-sizing: border-box; margin: 0; padding: 0; }
  html, body { width: 1200px; height: 1108px; overflow: hidden; }
  body { background: var(--page); position: relative; font-family: "Raleway", sans-serif; }

  .card { position: absolute; left: 219px; width: 774px; overflow: hidden; }
  .card--front { top: 50px; height: 473px; background: var(--photo-dark); }
  .card--back { top: 568px; height: 456px; background: var(--gold-back); }

  .front-photo {
    position: absolute; inset: 0;
    background: radial-gradient(ellipse at 60% 55%, var(--photo-mid) 0%, var(--photo-dark) 70%);
  }
  .front-wave { position: absolute; left: 0; top: 0; width: 774px; height: 473px; }

  .owner-name {
    position: absolute; left: 37px; top: 54px;
    font-family: "Playfair Display", serif; font-weight: 500;
    font-size: 30px; color: var(--gold-text); letter-spacing: 0.2px;
  }
  .owner-role { position: absolute; left: 37px; top: 92px; font-size: 18px; color: var(--white); }
  .service-line {
    position: absolute; left: 39px; top: 158px;
    font-size: 18px; line-height: 22px; color: var(--white);
  }
  .contact { position: absolute; left: 38px; font-size: 18.5px; color: var(--white); display: flex; align-items: center; gap: 10px; }
  .contact--phone { top: 254px; }
  .contact--web { top: 283px; }
  .contact svg { width: 18px; height: 18px; }
  .appointment { position: absolute; left: 38px; top: 321px; font-size: 18.5px; color: var(--gold-text); }

  .brand-name {
    position: absolute; font-family: "Raleway", sans-serif; font-weight: 300;
    color: var(--cream); text-align: center; line-height: 1;
  }
  .card--front .brand-name { left: 400px; width: 330px; top: 140px; font-size: 58px; }
  .card--back .brand-name { left: 180px; width: 400px; top: 148px; font-size: 68px; }
  .brand-name span { display: block; }
  .brand-name span + span { margin-top: 16px; }

  .brand-tagline {
    position: absolute; display: flex; justify-content: space-between;
    font-family: "Kreon", serif; color: var(--tag-yellow);
  }
  .card--front .brand-tagline { left: 404px; width: 310px; top: 294px; font-size: 27px; }
  .card--back .brand-tagline { left: 187px; width 380px; width: 380px; top: 324px; font-size: 31px; }
</style>
</head>
<body>

<section class="card card--front" aria-label="Business card front">
  <div class="front-photo" role="img" aria-label="Darkened photograph of a large two-storey house with a covered porch"></div>
  <svg class="front-wave" viewBox="0 0 774 473" aria-hidden="true">
    <path d="M0 398 C90 372 170 380 300 410 C430 440 540 470 640 460 C700 454 745 420 774 382 L774 473 L0 473 Z" fill="var(--gold)"/>
    <path d="M90 384 C190 378 300 400 420 432 C520 460 620 478 700 462 C740 454 762 440 774 430" fill="none" stroke="var(--ink)" stroke-width="6"/>
  </svg>

  <h1 class="owner-name">Daniel Trevick</h1>
  <p class="owner-role">Owner</p>
  <p class="service-line">Custom Interior &amp; Exterior<br>Window Treatments</p>

  <p class="contact contact--phone">
    <svg viewBox="0 0 20 20" aria-hidden="true"><path d="M2 7 C2 4 18 4 18 7 L18 9 L14 9 L14 7 L6 7 L6 9 L2 9 Z M5 10 L15 10 L17 17 L3 17 Z" fill="var(--white)"/></svg>
    919-555-0148
  </p>
  <p class="contact contact--web">
    <svg viewBox="0 0 20 20" aria-hidden="true"><circle cx="10" cy="10" r="8" fill="none" stroke="var(--white)" stroke-width="2"/><path d="M5 6 L9 5 L10 9 L7 12 Z M12 11 L15 12 L13 16 Z" fill="var(--white)"/></svg>
    GildedSlatworks.com
  </p>
  <p class="appointment">By Appointment</p>

  <div class="brand-name"><span>Gilded</span><span>Slatworks</span></div>
  <p class="brand-tagline"><span>Shutters</span><span>Shades</span><span>Blinds</span></p>
</section>

<section class="card card--back" aria-label="Business card back">
  <div class="brand-name"><span>Gilded</span><span>Slatworks</span></div>
  <p class="brand-tagline"><span>Shutters</span><span>Shades</span><span>Blinds</span></p>
</section>

</body>
</html>
```